Poster

I need a poster for my business, www.coastalsupperroutesnerja.example which some information about the most important activities (Sangria Tasting, Iberian Ham, Charcuteries & Sherry Wine Tasting, Sailboat Experiences and Picnic Experiences). A3 Format. Social media included (@coastalsupperroutescsr), contact information included.

```html
<!DOCTYPE html>
<html lang="en">
<head>
<meta charset="utf-8">
<title>Coastal Supper Routes — Poster</title>
<link rel="stylesheet" href="https://fonts.googleapis.com/css2?family=Bebas+Neue&family=Great+Vibes&family=Poppins:wght@400;500;600&display=swap">
<style>
  :root {
    --stage: #cdcdcd;
    --ink: #191613;
    --ink-warm: #231d17;
    --white: #ffffff;
    --amber: #f2a516;
    --amber-deep: #d98a0c;
    --muted: #d8d2c8;
  }
  * { margin: 0; padding: 0; box-sizing: border-box; }
  html, body { width: 1200px; height: 1033px; overflow: hidden; background: var(--stage); }
  .poster {
    position: absolute; left: 293px; top: 85px; width: 614px; height: 867px;
    background:
      radial-gradient(ellipse at 30% 85%, #2a221b 0%, transparent 55%),
      radial-gradient(ellipse at 75% 20%, #211b16 0%, transparent 60%),
      linear-gradient(180deg, var(--ink) 0%, var(--ink-warm) 100%);
    overflow: hidden;
    color: var(--white);
  }
  .headline { position: absolute; left: 0; top: 0; width: 100%; }
  .headline__enjoy {
    position: absolute; left: 0; width: 100%; top: 34px; text-align: center;
    font-family: "Great Vibes", cursive; font-size: 72px; line-height: 1;
    color: var(--amber); padding-right: 40px; z-index: 1;
  }
  .headline__city {
    position: absolute; left: 0; width: 100%; text-align: center;
    font-family: "Bebas Neue", sans-serif; font-weight: 400; line-height: 1; font-size: 121px;
    letter-spacing: 0.5px; color: var(--white);
  }
  .headline__city--first { top: 89px; }
  .headline__city--second { top: 191px; }
  .headline__amp {
    position: absolute; left: 295px; top: 173px; width: 36px; height: 36px;
    border-radius: 50%; background: var(--amber); color: var(--ink);
    font-family: "Poppins", sans-serif; font-weight: 600; font-size: 20px;
    display: flex; align-items: center; justify-content: center; z-index: 2;
  }
  .headline__tagline {
    position: absolute; left: 0; width: 100%; top: 294px; text-align: center;
    font-family: "Poppins", sans-serif; font-weight: 600; font-size: 14.5px;
    letter-spacing: 5.4px; color: var(--amber); padding-left: 6px;
  }
  .feature-photo { position: absolute; left: 55px; top: 330px; width: 495px; height: 330px; }
  .activities {
    position: absolute; left: 20px; top: 692px; width: 554px;
    display: flex; justify-content: space-between; list-style: none;
  }
  .activities__item {
    font-family: "Bebas Neue", sans-serif; font-size: 17px; line-height: 1.05;
    text-align: center; color: var(--white); padding: 0 8px; flex: 1;
  }
  .activities__item + .activities__item { border-left: 1px solid var(--amber-deep); }
  .activities__item:nth-child(3) { flex: 1.3; }
  .brand {
    position: absolute; left: 55px; top: 772px; display: flex; align-items: center; gap: 27px;
  }
  .brand__mark { width: 30px; height: 30px; background: var(--amber); }
  .brand__name {
    font-family: "Bebas Neue", sans-serif; font-size: 22px; line-height: 0.95; color: var(--white);
  }
  .contact { position: absolute; right: 55px; top: 784px; text-align: right; }
  .contact__social { font-family: "Poppins", sans-serif; font-size: 13.5px; letter-spacing: 1.5px; color: var(--muted); }
  .contact__social-label { font-size: 8.5px; letter-spacing: 1.3px; margin-right: 12px; color: var(--white); }
  .contact__web {
    margin-top: 8px; font-family: "Poppins", sans-serif; font-size: 12.6px;
    letter-spacing: 1.2px; color: var(--white);
  }
  .contact__web em { font-style: normal; color: var(--amber); }
</style>
</head>
<body>
  <main class="poster">
    <header class="headline">
      <div class="headline__enjoy">Enjoy</div>
      <h1 class="headline__city headline__city--first">MARBELLA</h1>
      <span class="headline__amp">&amp;</span>
      <h1 class="headline__city headline__city--second">ESTEPONA</h1>
      <p class="headline__tagline">WITH COASTAL SUPPER ROUTES</p>
    </header>

    <svg class="feature-photo" viewBox="0 0 500 350" preserveAspectRatio="none" role="img" aria-label="Overhead photo of a roasted chicken with tomatoes and basil on a wooden board, a plate of corn and carrots, and small bowls of side dishes">
      <defs>
        <radialGradient id="dish-glow" cx="62%" cy="40%" r="60%">
          <stop offset="0%" stop-color="#b8742e"/>
          <stop offset="35%" stop-color="#7a4522"/>
          <stop offset="70%" stop-color="#3a2a20"/>
          <stop offset="100%" stop-color="#201a16"/>
        </radialGradient>
        <radialGradient id="veg-glow" cx="22%" cy="45%" r="30%">
          <stop offset="0%" stop-color="#e0a030" stop-opacity="0.75"/>
          <stop offset="100%" stop-color="#e0a030" stop-opacity="0"/>
        </radialGradient>
      </defs>
      <path d="M40 130 L120 45 L230 10 L330 5 L390 40 L450 25 L485 110 L470 200 L420 260 L340 280 L280 300 L190 295 L120 250 L60 230 L10 180 Z" fill="url(#dish-glow)"/>
      <path d="M40 130 L120 45 L230 10 L330 5 L390 40 L450 25 L485 110 L470 200 L420 260 L340 280 L280 300 L190 295 L120 250 L60 230 L10 180 Z" fill="url(#veg-glow)"/>
    </svg>

    <ul class="activities">
      <li class="activities__item">Sangria<br>Tasting</li>
      <li class="activities__item">Iberian<br>Ham</li>
      <li class="activities__item">Charcuteries<br>&amp; Sherry<br>Wine Tasting</li>
      <li class="activities__item">Sailboat<br>Experiences</li>
      <li class="activities__item">Picnic<br>Experiences</li>
    </ul>

    <footer>
      <div class="brand">
        <span class="brand__mark"></span>
        <span class="brand__name">COASTAL SUPPER<br>ROUTES</span>
      </div>
      <div class="contact">
        <p class="contact__social"><span class="contact__social-label">follow us on</span>@coastalsupperroutescsr</p>
        <p class="contact__web">www.<em>coastalsupperroutesnerja</em>.example</p>
      </div>
    </footer>
  </main>
</body>
</html>
```